Kestrel - Transport company looking for a basic but smart design for the sides of our trailers

We have a logo 'Kestrel' which i would like to keep.
We have 2 companies Kestrel Haulage - Maroon signwriting (general freight ) and Kestrel Refrigerated - Blue signwriting (refrigerated freight) that can share the same design.
I'd like to come up with a basic modern design that will incorporate the Kestrel logo, the company name and the website and maybe an image at the front od some sort, a 3D swish or a stripe or something.
The Kestrel Haulage maroon trailers are too busy and I don't like the icicles on the front of the Kestrel Refrigerated blue trailers.

```html
<!DOCTYPE html>
<html lang="en">
<head>
<meta charset="utf-8">
<title>Kestrel Refrigerated – Trailer Side Design</title>
<link rel="stylesheet" href="https://fonts.googleapis.com/css2?family=Exo+2:ital,wght@0,800;1,800&family=Open+Sans:wght@500&display=swap">
<style>
  :root {
    --backdrop: #6393cb;
    --panel: #ffffff;
    --brand-blue: #26337a;
    --frost-soft: rgba(38, 51, 122, 0.10);
    --frost-faint: rgba(38, 51, 122, 0.04);
  }
  * { margin: 0; padding: 0; box-sizing: border-box; }
  html, body {
    width: 1200px;
    height: 1000px;
    overflow: hidden;
    background: var(--backdrop);
  }
  .canvas {
    position: relative;
    width: 1200px;
    height: 1000px;
    background: var(--backdrop);
  }
  .trailer-side {
    position: absolute;
    left: 50px;
    top: 317px;
    width: 1100px;
    height: 367px;
    background: var(--panel);
    overflow: hidden;
  }
  .company-block {
    position: absolute;
    left: 34px;
    top: 29px;
    color: var(--brand-blue);
    z-index: 2;
  }
  .company-name {
    font-family: "Exo 2", sans-serif;
    font-weight: 800;
    font-style: italic;
    font-size: 24px;
    line-height: 1;
    text-transform: uppercase;
  }
  .company-web {
    font-family: "Open Sans", sans-serif;
    font-weight: 500;
    font-size: 18px;
    line-height: 1.2;
    margin-top: 1px;
  }
  .frost-pattern {
    position: absolute;
    left: 28px;
    top: 66px;
    width: 760px;
    height: 280px;
    background:
      radial-gradient(circle at 4% 52%, var(--frost-soft) 0 14px, transparent 15px),
      radial-gradient(circle at 24% 50%, var(--frost-soft) 0 10px, transparent 11px),
      radial-gradient(circle at 38% 22%, var(--frost-soft) 0 14px, transparent 15px),
      radial-gradient(circle at 62% 22%, var(--frost-soft) 0 14px, transparent 15px),
      radial-gradient(circle at 83% 7%, var(--frost-soft) 0 18px, transparent 19px),
      radial-gradient(circle at 18% 82%, var(--frost-soft) 0 18px, transparent 19px),
      radial-gradient(circle at 47% 84%, var(--frost-soft) 0 22px, transparent 23px),
      radial-gradient(circle at 77% 88%, var(--frost-soft) 0 24px, transparent 25px),
      radial-gradient(ellipse at 45% 50%, var(--frost-faint) 0%, transparent 75%);
  }
  .brand-name {
    position: absolute;
    right: 32px;
    top: 118px;
    font-family: "Exo 2", sans-serif;
    font-weight: 800;
    font-size: 112px;
    line-height: 1;
    color: var(--brand-blue);
    text-transform: uppercase;
    z-index: 2;
  }
</style>
</head>
<body>
<main class="canvas">
  <section class="trailer-side">
    <div class="company-block">
      <p class="company-name">Kestrel Refrigerated</p>
      <p class="company-web">www.kestrelhaulage.com.au</p>
    </div>
    <div class="frost-pattern" role="img" aria-label="Scattered navy snowflakes of varying sizes across the left and centre of the panel"></div>
    <p class="brand-name">Kestrel</p>
  </section>
</main>
</body>
</html>
```